established boer goat stud and dorper sheep stud need an updated look

I need a design to promote the boer goat stud and dorper sheep stud, so its clear and simple
Updates

Details for business card design Wirrabel Boers and Dorper Sheep Stud. I would like silhouette animal head or full body of a boer goat (not a dairy breed goat) and Dorper sheep. Contact: Maree Dalton +61 412578304 Sandra Pollock +61 438615027 Mooroopna North Victoria Australia Email: wirrabel5184@mailvane.com

Industry/Entity Type

Agriculture

Contact Information for Business Card

Wirrabel Boers and Dorper Sheep Stud Maree Dalton +61 412578304 Sandra Pollock +61 438615027 wirrabel5184@mailvane.com Kerrabee Flat Victoria Australia

Colors
EE7325
F08F49
F5BC92
FAE3D3
FDF4ED

Requirements
Must have
• My Boer Goats and Dorper Sheep images see my photos

```html
<!DOCTYPE html>
<html lang="en">
<head>
<meta charset="utf-8">
<title>Wirrabel Boers and Dorper Sheep Stud – Business Card</title>
<link rel="stylesheet" href="https://fonts.googleapis.com/css2?family=Lobster&family=Tinos&display=swap">
<style>
  :root {
    --page: #d8b898;
    --orange: #e4772f;
    --orange-deep: #c85a1c;
    --orange-text: #d9651f;
    --cream: #f4ede7;
    --white: #fdf4ed;
    --grass-dark: #46542a;
    --grass: #5f7a32;
  }
  * { box-sizing: border-box; margin: 0; padding: 0; }
  html, body { width: 1200px; height: 800px; overflow: hidden; }
  body {
    background: var(--page);
    display: flex;
    flex-direction: column;
    align-items: center;
    justify-content: center;
    gap: 36px;
  }
  .card {
    position: relative;
    width: 560px;
    height: 320px;
    overflow: hidden;
    box-shadow: 0 10px 26px rgba(80, 50, 25, 0.25);
  }

  /* Front */
  .card-front .photo {
    position: absolute;
    inset: 0;
    background: linear-gradient(160deg, var(--grass) 0%, var(--grass-dark) 100%);
  }
  .card-front .title-band {
    position: absolute;
    left: 0; right: 0;
    top: 122px;
    height: 64px;
    background: var(--cream);
    display: flex;
    align-items: center;
    gap: 12px;
    padding: 0 18px;
  }
  .title-band .rule {
    flex: 1;
    height: 1px;
    background: var(--orange-text);
    margin-top: 12px;
  }
  .title-band .brand-script {
    font-family: "Lobster", cursive;
    font-size: 27px;
    color: var(--orange-text);
    white-space: nowrap;
  }

  /* Back */
  .card-back {
    background: linear-gradient(135deg, var(--orange) 0%, #e07029 55%, var(--orange-deep) 100%);
    color: var(--white);
    font-family: "Tinos", serif;
  }
  .card-back .heading {
    position: absolute;
    left: 0; right: 0;
    top: 120px;
    display: flex;
    align-items: flex-end;
    gap: 10px;
  }
  .heading .rule-short { width: 22px; height: 1px; background: var(--white); margin-bottom: 6px; }
  .heading .rule-long { flex: 1; height: 1px; background: var(--white); margin-bottom: 22px; }
  .heading .brand-name { font-size: 19px; white-space: nowrap; }
  .contact-list {
    position: absolute;
    left: 40px;
    top: 176px;
    list-style: none;
    font-size: 13px;
    line-height: 1.35;
  }
  .contact-list li { display: flex; gap: 10px; align-items: flex-start; margin-bottom: 8px; }
  .contact-list .icon {
    flex: none;
    width: 16px; height: 16px;
    margin-top: 1px;
  }
</style>
</head>
<body>

  <section class="card card-front">
    <div class="photo" role="img" aria-label="Photograph of a Dorper sheep standing on grass"></div>
    <div class="title-band">
      <span class="rule"></span>
      <span class="brand-script">Wirrabel Boers and Dorper Sheep Stud</span>
      <span class="rule"></span>
    </div>
  </section>

  <section class="card card-back">
    <div class="heading">
      <span class="rule-short"></span>
      <span class="brand-name">Wirrabel Boers and Dorper Sheep Stud</span>
      <span class="rule-long"></span>
    </div>
    <ul class="contact-list">
      <li>
        <svg class="icon" viewBox="0 0 16 16" aria-hidden="true"><circle cx="8" cy="8" r="8" fill="#fdf4ed"/><rect x="5.5" y="3.5" width="5" height="9" rx="1" fill="none" stroke="#e4772f" stroke-width="1.2"/><circle cx="8" cy="10.8" r="0.6" fill="#e4772f"/></svg>
        <span>Maree Dalton +61 412578304<br>Sandra Pollock +61 438615027</span>
      </li>
      <li>
        <svg class="icon" viewBox="0 0 16 16" aria-hidden="true"><circle cx="8" cy="8" r="8" fill="#fdf4ed"/><path d="M6.8 9.2l2.4-2.4M7.6 5.6l1-1a1.6 1.6 0 0 1 2.3 2.3l-1 1M8.4 10.4l-1 1a1.6 1.6 0 0 1-2.3-2.3l1-1" fill="none" stroke="#e4772f" stroke-width="1.2" stroke-linecap="round"/></svg>
        <span>wirrabel5184@mailvane.com</span>
      </li>
      <li>
        <svg class="icon" viewBox="0 0 16 16" aria-hidden="true"><circle cx="8" cy="8" r="8" fill="#fdf4ed"/><path d="M8 12.5s-3-3.2-3-5.5a3 3 0 0 1 6 0c0 2.3-3 5.5-3 5.5z" fill="#e4772f"/><circle cx="8" cy="7" r="1.1" fill="#fdf4ed"/></svg>
        <span>Kerrabee Flat Victoria Australia</span>
      </li>
    </ul>
  </section>

</body>
</html>
```